Commercial Loan Originator Business Card (CHANGE COLORS SCHEME)

CHANGE COLOR SCHEME - SAME DESIGN

Name Marlene Agate
Title Commercial Loan Originator
Office (800) 417-2906 x68
Direct (240) 615-2043
Email freshgreens4life@quillbox.example

Name Dale Morrow
Office (800) 417-2906 x70
Direct (410) 392-5184
Email d.morthehomeguy@quillbox.example

Name Leonard Vasko
Office (800) 417-2906 x71
Direct (215) 463-0712
Email l.vasko41@quillbox.example

Name Gwen Halsey
Office (800) 417-2906 x
Direct (202) 548-1370
Email ghalsey63@quillbox.example

Name Mirna Ashby
Office (800) 417-2906 x72
Direct (240) 871-4526
Email tristatehomelending@quillbox.example

```html
<!DOCTYPE html>
<html lang="en">
<head>
<meta charset="utf-8">
<title>Mirna Ashby – Commercial Loan Originator</title>
<link href="https://fonts.googleapis.com/css2?family=Montserrat:wght@400;700&display=swap" rel="stylesheet">
<style>
  :root {
    --accent: #0e5f57;
    --accent-soft: #c9a44c;
    --ink: #26332f;
    --card: #ffffff;
    --stage: #e6e9e7;
    --photo-top: #f3f4f3;
    --photo-mid: #3b3336;
    --photo-low: #1c1a1b;
  }
  html, body {
    margin: 0;
    width: 1200px;
    height: 788px;
    overflow: hidden;
    background: var(--stage);
    font-family: "Montserrat", Arial, sans-serif;
  }
  .card {
    position: absolute;
    left: 100px;
    top: 108px;
    width: 1000px;
    height: 572px;
    background: var(--card);
    border-radius: 30px;
    border-left: 6px solid var(--accent);
    border-bottom: 7px solid var(--accent);
    box-sizing: border-box;
    overflow: hidden;
    box-shadow: 0 14px 34px rgba(14, 40, 36, 0.18);
  }
  .identity {
    position: absolute;
    left: 64px;
    top: 62px;
  }
  .name {
    margin: 0;
    color: var(--accent);
    font-weight: 700;
    font-size: 42px;
    letter-spacing: 0.5px;
    text-transform: uppercase;
    line-height: 1;
  }
  .title {
    margin: 8px 0 0;
    color: var(--ink);
    font-weight: 400;
    font-size: 21px;
    letter-spacing: 0.3px;
  }
  .rule {
    width: 64px;
    height: 3px;
    margin-top: 14px;
    background: var(--accent-soft);
  }
  .contacts {
    position: absolute;
    left: 64px;
    top: 410px;
    margin: 0;
    padding: 0;
    list-style: none;
  }
  .contact {
    display: flex;
    align-items: center;
    gap: 12px;
    color: var(--ink);
    font-size: 22px;
    font-weight: 400;
    line-height: 1;
    margin-bottom: 16px;
    white-space: nowrap;
  }
  .contact svg {
    width: 20px;
    height: 20px;
    flex: none;
    fill: var(--accent);
  }
  .portrait {
    position: absolute;
    right: 0;
    bottom: 0;
    width: 380px;
    height: 430px;
    border-radius: 190px 190px 0 0;
    background: linear-gradient(180deg, var(--photo-top) 0%, var(--photo-mid) 40%, var(--photo-low) 100%);
  }
</style>
</head>
<body>
  <article class="card">
    <header class="identity">
      <h1 class="name">Mirna Ashby</h1>
      <p class="title">Commercial Loan Originator</p>
      <div class="rule"></div>
    </header>

    <ul class="contacts">
      <li class="contact">
        <svg viewBox="0 0 24 24" aria-hidden="true"><path d="M6.6 10.8a15.1 15.1 0 0 0 6.6 6.6l2.2-2.2a1 1 0 0 1 1-.25 11.4 11.4 0 0 0 3.6.57 1 1 0 0 1 1 1V20a1 1 0 0 1-1 1A17 17 0 0 1 3 4a1 1 0 0 1 1-1h3.5a1 1 0 0 1 1 1c0 1.25.2 2.45.57 3.57a1 1 0 0 1-.25 1z"/></svg>
        <span>(800) 417-2906 x72</span>
      </li>
      <li class="contact">
        <svg viewBox="0 0 24 24" aria-hidden="true"><path d="M7 1h10a2 2 0 0 1 2 2v18a2 2 0 0 1-2 2H7a2 2 0 0 1-2-2V3a2 2 0 0 1 2-2zm0 3v14h10V4zm5 15.2a1.2 1.2 0 1 0 0 2.4 1.2 1.2 0 0 0 0-2.4z"/></svg>
        <span>(240) 871-4526</span>
      </li>
      <li class="contact">
        <svg viewBox="0 0 24 24" aria-hidden="true"><path d="M2 5h20v14H2zm2 2v.4l8 5.3 8-5.3V7zm0 2.8V17h16V9.8l-8 5.3z"/></svg>
        <span>tristatehomelending@quillbox.example</span>
      </li>
    </ul>

    <div class="portrait" role="img" aria-label="Portrait photo of the loan originator, seated, wearing a black sleeveless top"></div>
  </article>
</body>
</html>
```